Computer consultant website

Plimvex Software is a newly started computer consulting company. It's a small one-man company that provides mostly Android applications but also websites in collaboration with designers. I'm running this company on the side of full time university studies.

I'm in need of a website which will function as:
Primarily - I'll direct potential clients to the page so they can read about the company, what i offer and past work.
Secondarily - Making my company visible through the web and maybe getting new clients.

The final design should look modern, clean and professional.

Pages that will be in the final website are (Note that it's not the exact titles as the page will not be in english):
* About
* Services (what Plimvex offers)
* Portfolio/work
* Short news (like ArtHivers "News and press")
* Contact.

Inspiration
http://www.arthiver.example/design/87836
http://www.brookwellstudio.example/
http://www.arthiver.example/design/845881
http://www.arthiver.example/design/1369424 - Lighter design, however a bit cluttered.

No programming code is needed delivered at all. Focus on designing rather then coding.

If you have any questions, do not hesitate to send me a message.

Target Market(s)

Non-technical entrepreneurs and small companies.

Industry/Entity Type

University

Requirements
Must have
• Must have my company logo (see attachment).

Must in any way use both colors from my logo.

A way to logically rearrange content to fit smaller screens. I will implement this design so that it can be pleasantly viewed on mobile devices. You don't necessarily need to provide exactly how the design would look on mobile devices.

I need the following types of page designs:
* Landing page
* Content page
* Portfolio/work (with accompanying inside/clicked) page

Landing/start page must in any way include at least the information:
* Shorter version of "About Plimvex"
* At least 1 most recent portfolio/work entry
* At least 1 most recent news entry
* Services that Plimvex offers.
Nice to have
• -
Should not have
• Testimonials or newsletter.

```html
<!DOCTYPE html>
<html lang="en">
<head>
<meta charset="utf-8">
<title>Plimvex – Mobile applications &amp; websites</title>
<link href="https://fonts.googleapis.com/css2?family=Roboto:wght@300;400;500&family=Arimo:wght@400;700&display=swap" rel="stylesheet">
<style>
:root{
  --blue:#1a73e8;
  --blue-deep:#0b47b8;
  --blue-hero-top:#2a7fee;
  --blue-hero-bottom:#0c4dc0;
  --ink:#333333;
  --ink-soft:#555555;
  --muted:#9a9a9a;
  --orange:#f28a00;
  --orange-light:#f9a51f;
  --band:#f2f2f2;
  --line:#d9d9d9;
  --dark:#333333;
  --dark-btn:#2b2b2b;
  --footer-text:#e0e0e0;
}
*{margin:0;padding:0;box-sizing:border-box}
html,body{width:1029px;height:1200px;overflow:hidden;background:#fff}
body{position:relative;font-family:"Arimo",Arial,sans-serif;color:var(--ink)}
.abs{position:absolute}
.heading{font-family:"Roboto",Arial,sans-serif;font-weight:400;font-size:23px;color:var(--ink)}
.heading span{color:var(--blue)}

/* header */
.site-header{position:absolute;left:0;top:0;width:1029px;height:93px;background:#fff}
.brand{position:absolute;left:103px;top:28px;display:flex;align-items:center;gap:10px}
.brand-mark{width:34px;height:34px;border-radius:50%;background:var(--blue)}
.brand-name{font-family:"Roboto",Arial,sans-serif;font-weight:500;font-size:32px;color:var(--ink);letter-spacing:-0.5px}
.main-nav{position:absolute;right:103px;top:53px;display:flex;gap:28px;font-family:"Roboto",Arial,sans-serif;font-size:12px}
.main-nav a{color:var(--ink);text-decoration:none}
.main-nav a.active{color:var(--blue)}

/* hero */
.hero{position:absolute;left:0;top:93px;width:1029px;height:338px;
  background:radial-gradient(ellipse at 60% 30%, #3b8ff5 0%, var(--blue-hero-top) 35%, var(--blue-hero-bottom) 100%)}
.hero-title{position:absolute;left:103px;top:68px;font-family:"Roboto",Arial,sans-serif;font-weight:400;font-size:24px;color:#fff;white-space:nowrap}
.hero-text{position:absolute;left:104px;top:116px;width:283px;font-size:12px;line-height:14.3px;color:#fff;text-align:justify}
.btn-orange{position:absolute;left:103px;top:250px;width:140px;height:35px;border-radius:3px;
  background:linear-gradient(var(--orange-light),var(--orange));color:#fff;font-family:"Roboto",Arial,sans-serif;font-size:16px;
  display:flex;align-items:center;justify-content:center}
.hero-visual{position:absolute;left:463px;top:40px;width:459px;height:261px;border-radius:18px;
  background:linear-gradient(90deg,rgba(120,170,240,.35),rgba(40,40,40,.7) 20%,rgba(60,60,60,.75) 50%,rgba(110,100,100,.7) 80%,rgba(40,80,160,.2))}
.hero-arrow{position:absolute;top:145px}

/* welcome */
.welcome-title{left:104px;top:456px}
.welcome-text{position:absolute;left:104px;width:545px;font-size:10px;line-height:12.3px;letter-spacing:.6px;color:var(--ink-soft);text-align:justify}
.btn-small{position:absolute;width:80px;height:23px;border-radius:6px 0 6px 0;color:#fff;font-family:"Roboto",Arial,sans-serif;font-size:11px;display:flex;align-items:center;justify-content:center}
.btn-blue{background:var(--blue)}
.btn-dark{background:var(--dark-btn)}

/* services */
.services-title{left:711px;top:456px}
.service-list{position:absolute;left:711px;top:498px;list-style:none;font-family:"Roboto",Arial,sans-serif;font-size:12.5px;color:var(--ink-soft)}
.service-list li{height:24px;display:flex;align-items:center;gap:9px}
.service-list li::before{content:"";width:8px;height:8px;border:2px solid var(--blue);border-radius:50%}

/* quick contact */
.quick-contact{position:absolute;left:0;top:709px;width:1029px;height:80px;background:var(--band);border-top:1px solid var(--line);border-bottom:1px solid var(--line)}
.qc-title{position:absolute;left:103px;top:10px;font-family:"Roboto",Arial,sans-serif;font-size:18px;color:var(--ink)}
.qc-title small{font-size:12px;color:var(--ink-soft)}
.field{position:absolute;top:38px;width:232px;height:29px;background:#fff;border:1px solid #cfcfcf;border-radius:2px;font-family:"Roboto",Arial,sans-serif;font-size:12px;color:#888;padding-left:10px;display:flex;align-items:center;letter-spacing:.5px}
.btn-submit{position:absolute;left:830px;top:37px;width:97px;height:32px;border-radius:3px;background:linear-gradient(#2a84f0,var(--blue-deep));color:#fff;font-family:"Roboto",Arial,sans-serif;font-weight:500;font-size:15px;display:flex;align-items:center;justify-content:center}

/* news */
.news-title{left:104px;top:816px}
.news-date{position:absolute;left:161px;top:862px;font-family:"Roboto",Arial,sans-serif;font-size:12.5px;color:var(--blue)}
.news-head{position:absolute;left:161px;top:882px;font-size:12.5px;letter-spacing:.5px;color:var(--ink)}
.news-text{position:absolute;left:161px;top:897px;width:305px;font-family:"Roboto",Arial,sans-serif;font-weight:300;font-size:12px;line-height:16.5px;color:var(--muted)}
.link-blue{position:absolute;font-size:10px;letter-spacing:.5px;color:var(--blue)}

/* projects */
.projects-title{left:565px;top:816px}
.project-caption{position:absolute;top:853px;font-family:"Roboto",Arial,sans-serif;font-size:12px;color:var(--ink-soft)}
.project-thumb{position:absolute;top:871px;width:171px;height:105px;border:1px solid #d5d5d5;background:#fff;padding:5px;box-shadow:0 6px 6px -4px rgba(0,0,0,.2)}
.project-thumb div{width:100%;height:100%}

/* footer */
.site-footer{position:absolute;left:0;top:1019px;width:1029px;height:181px;background:var(--dark)}
.footer-col{position:absolute;top:19px}
.footer-col h4{font-family:"Roboto",Arial,sans-serif;font-weight:400;font-size:12px;color:#fff;margin-bottom:19px}
.footer-col a{display:block;font-size:10px;letter-spacing:.7px;color:var(--footer-text);text-decoration:none;height:20.5px}
.social{position:absolute;right:103px;top:24px;display:flex;gap:12px}
.social span{width:18px;height:18px;border-radius:50%;background:#8a8a8a}
.social span.on{background:#fff}
.copyright{position:absolute;right:103px;top:121px;text-align:right;font-size:10px;letter-spacing:.7px;color:var(--footer-text);line-height:17px}
</style>
</head>
<body>

<header class="site-header">
  <div class="brand"><span class="brand-mark"></span><span class="brand-name">Plimvex</span></div>
  <nav class="main-nav">
    <a class="active" href="#">Home</a><a href="#">About</a><a href="#">Services</a><a href="#">Portfolio</a><a href="#">News</a><a href="#">Contact</a>
  </nav>
</header>

<section class="hero">
  <svg class="hero-arrow" style="left:24px" width="30" height="48" viewBox="0 0 30 48"><polyline points="28,2 4,24 28,46" fill="none" stroke="#9cc4fa" stroke-width="3"/></svg>
  <svg class="hero-arrow" style="left:973px" width="30" height="48" viewBox="0 0 30 48"><polyline points="2,2 26,24 2,46" fill="none" stroke="#9cc4fa" stroke-width="3"/></svg>
  <h1 class="hero-title">Developed Mobile Applications</h1>
  <p class="hero-text">Lorem ipsum dolor sit amet, consectetur adipiscing elit. Duis vitae lectus sit amet turpis molestie tempor. Vestibulum sollicitudin nibh sodales leo porta nec adipiscing turpis tempus. Vestibulum mollis purus augue. Vestibulum ultricies nisl purus, nec dapibus purus.</p>
  <div class="btn-orange">Read More</div>
  <div class="hero-visual" role="img" aria-label="Three smartphones showing home screen, clock and music player apps"></div>
</section>

<h2 class="heading abs welcome-title">Welcome to <span>Plimvex</span></h2>
<p class="welcome-text" style="top:501px">Lorem ipsum dolor sit amet, consectetur adipiscing elit. Curabitur ligula massa, aliquam id commodo quis, consectetur eu odio. Phasellus ac lobortis felis. Aliquam lobortis rutrum ipsum vel suscipit. Nunc auctor aliquet mi nec blandit. Maecenas nec egestas tellus. Cras dapibus mauris nec dui dapibus sollicitudin. Vestibulum eu tortor ac leo lobortis interdum. Praesent leo nisl, auctor sit amet aliquam ornare, blandit et nulla. Cras posuere quam velit, at hendrerit est. Quisque a augue sit amet eros ultricies ultricies.</p>
<p class="welcome-text" style="top:578px">Lorem ipsum dolor sit amet, consectetur adipiscing elit. Curabitur ligula massa, aliquam id commodo quis, consectetur eu odio. Phasellus ac lobortis felis. Aliquam lobortis rutrum ipsum vel suscipit. Nunc auctor aliquet mi nec blandit. Maecenas nec egestas tellus. Cras dapibus mauris nec dui dapibus sollicitudin. Vestibulum eu tortor ac leo lobortis interdum.</p>
<div class="btn-small btn-blue" style="left:567px;top:647px">Read More</div>

<h2 class="heading abs services-title">Our <span>Services</span></h2>
<ul class="service-list">
  <li>Pellentesque vulputate</li><li>Nulla vulputate dolor</li><li>Nunc eget lorem</li><li>Nunc ac diam a tortor</li><li>Cras quis nisi in ligula</li><li>Etiam id augue</li>
</ul>
<div class="btn-small btn-dark" style="left:845px;top:647px">Read More</div>

<section class="quick-contact">
  <div class="qc-title">Quick Contact... <small>Leave your details and</small> we will contact you.</div>
  <div class="field" style="left:103px">Your Full Name</div>
  <div class="field" style="left:345px">Phone Number</div>
  <div class="field" style="left:588px">Email</div>
  <div class="btn-submit">Submit</div>
</section>

<h2 class="heading abs news-title">Latest <span>News</span></h2>
<svg class="abs" style="left:104px;top:861px" width="42" height="42" viewBox="0 0 42 42">
  <rect x="1.5" y="5" width="39" height="35" rx="4" fill="#fff" stroke="#555" stroke-width="3"/>
  <rect x="1.5" y="5" width="39" height="9" fill="#555"/>
  <rect x="10" y="1" width="4" height="9" rx="1" fill="#555"/><rect x="28" y="1" width="4" height="9" rx="1" fill="#555"/>
  <text x="21" y="35" text-anchor="middle" font-family="Roboto,Arial,sans-serif" font-size="19" font-weight="500" fill="#1a73e8">27</text>
</svg>
<div class="news-date">27 February 2013</div>
<div class="news-head">Lorem ipsum dolor sit amet</div>
<p class="news-text">Consectetur adipiscing elit. Duis vitae lectus sit amet turpis molestie tempor. Vestibulum sollicitudin nibh sodales leo porta nec adipiscing turpis tempus.</p>
<span class="link-blue" style="left:404px;top:954px">Read More &gt;</span>

<h2 class="heading abs projects-title">Recent <span>Projects</span></h2>
<span class="link-blue" style="left:883px;top:828px">View All &gt;</span>
<div class="project-caption" style="left:567px">Lorem ipsum dolor</div>
<div class="project-caption" style="left:758px">Lorem ipsum dolor</div>
<div class="project-thumb" style="left:566px"><div role="img" aria-label="Screenshot of a conversion-optimisation website project" style="background:linear-gradient(#fff 18%,#2a9cc4 18%,#2a9cc4 72%,#f4f4f4 72%)"></div></div>
<div class="project-thumb" style="left:755px"><div role="img" aria-label="Screenshot of the Plimvex website project" style="background:linear-gradient(#fff 18%,#1a73e8 18%,#0c4dc0 68%,#f6f6f6 68%)"></div></div>

<footer class="site-footer">
  <div class="footer-col" style="left:103px"><h4>MAIN</h4><a href="#">Home</a><a href="#">About</a><a href="#">Services</a><a href="#">Portfolio</a><a href="#">News</a></div>
  <div class="footer-col" style="left:225px"><h4>COMPANY</h4><a href="#">About us</a><a href="#">Help</a><a href="#">Support</a><a href="#">Jobs</a><a href="#">Contact us</a></div>
  <div class="footer-col" style="left:352px"><h4>SERVICES</h4><a href="#">Lorem Ipsum</a><a href="#">Ipsum sit</a><a href="#">Sit Amet</a><a href="#">Lorem Amet</a></div>
  <div class="social"><span></span><span class="on"></span><span></span></div>
  <div class="copyright">© 2012 Plimvex.<br>Privacy Policy &nbsp;|&nbsp; Terms of Service</div>
</footer>

</body>
</html>
```